Classy, Elegant, Simple Business Card Design

Looking to have a classy, simple, and elegant design. Want a top notch designed business card. I really like the look of the new torvane credit card. I also like the design I attached. I am trying to reach 21-29 year old females for booking us for there wedding or event. We offer Disc Jockey Service, Photo Booth Rentals, and Uplighting .

Target Market(s)

21-28 year old females

Contact Information for Business Card

Has to have logo, website, email, and phone number

Font styles to use
Other font styles liked:
• open to font choice, modern, clean
Designer to choose
33a6d7
0791cd
0555a3
ffffff

Requirements
Must have
• Has to have logo, website, email, and phone number
Nice to have
• I really like the design of the new torvane credit card. I also included my logo and some designs I like
Should not have
• clutter or too much info

```html
<!DOCTYPE html>
<html lang="en">
<head>
<meta charset="utf-8">
<title>Tidelight Event Group — Business Card</title>
<link href="https://fonts.googleapis.com/css2?family=Jost:wght@400;500&display=swap" rel="stylesheet">
<style>
  :root {
    --backdrop: #b3b3b3;
    --card: #fbfbfb;
    --ink-silver: #9a9a9a;
    --ink-contact: #8c8c8c;
    --shadow: rgba(0, 0, 0, 0.22);
  }
  html, body {
    margin: 0;
    padding: 0;
    width: 1200px;
    height: 900px;
    overflow: hidden;
    background: var(--backdrop);
    font-family: "Jost", "Futura", sans-serif;
  }
  .canvas {
    position: relative;
    width: 1200px;
    height: 900px;
  }
  .card {
    position: absolute;
    left: 292px;
    width: 616px;
    height: 352px;
    border-radius: 18px;
    background: var(--card);
    box-shadow: 0 6px 14px var(--shadow);
  }
  .card--front { top: 76px; }
  .card--back { top: 472px; }

  .brand-name {
    position: absolute;
    left: 0;
    right: 0;
    top: 158px;
    margin: 0;
    text-align: center;
    font-weight: 400;
    font-size: 30px;
    letter-spacing: 4px;
    color: var(--ink-silver);
  }
  .brand-mark {
    position: absolute;
    left: 42px;
    top: 44px;
    margin: 0;
    font-weight: 400;
    font-size: 30px;
    color: var(--ink-silver);
  }
  .contact {
    position: absolute;
    left: 318px;
    top: 200px;
    color: var(--ink-contact);
  }
  .contact__name {
    margin: 0 0 12px;
    font-weight: 500;
    font-size: 20px;
    letter-spacing: 0.5px;
  }
  .contact__line {
    margin: 0;
    font-weight: 400;
    font-size: 15.5px;
    line-height: 25px;
    letter-spacing: 0.2px;
  }
</style>
</head>
<body>
  <main class="canvas">
    <section class="card card--front" aria-label="Card front">
      <p class="brand-name">TIDELIGHT EVENT GROUP</p>
    </section>

    <section class="card card--back" aria-label="Card back">
      <p class="brand-mark">Tidelight</p>
      <div class="contact">
        <p class="contact__name">Daniel K. Harlow</p>
        <p class="contact__line">555 014 2390</p>
        <p class="contact__line">hello@tidelighteventgroup.com</p>
        <p class="contact__line">www.tidelighteventgroup.com</p>
      </div>
    </section>
  </main>
</body>
</html>
```